TRELOS - Web Design Project

Task Description
RELOS is the major GLOVRA project supporting the Indonesian Bureau of Tidal Works and Harvests (BTWH). BTWH is responsible for promoting sustainable use of fish and other marine resources for Indonesia’s long-term economic prosperity. Its mandate encompasses such issues as drafting of marine and fisheries sector policies; control of overfishing, destructive and illegal fishing practices; spatial planning for resource use; management of conservation areas; data analysis and modeling for fisheries management; and promoting the long-term welfare of fishing communities. The TRELOS project is supporting BTWH efforts to achieve sustainability in the marine and fisheries sector and to improve the response of coastal communities to near-term disasters and long-term impacts related to climate change.

The TRELOS project has three key thematic areas: [policy] [1], [sustainable fisheries] [2], and [climate change] [3] — as well as supporting overall coordination of [Coastal Stewardship Scheme] [4] activities.
Updates

Project Deadline Extended
Reason: There are two public holidays in Indonesia so we are unable to provide feedback to designers between 17th and the 20th.

a few people have asked for reference sites - there is really no reference site we can give but I have attached a jpg for some ideas - we are after innovated ideas that will capture people's attention but which is extermely easy to use and navigate. 

the main focus should be on a map on Indonesia with focal points of our three offices (and with great navigation buttons/tools). 

please give us something amazing and use your design skills to make an amazing site

thanks

Target Market(s)

under 25, college or uni - research students - others interested in marine and fisheries

Industry/Entity Type

Sustainability

Requirements
Must have
• The web must have Indonesia map on the center with button on Jakarta city as headquarter, Sulawesi Tenggara (Wakatobi) as branch office and Nusa Tenggara Barat (Mataram), must have an icon for navigation on the upper, left or bottom side. Example of layout is attached (only as example). The "buttons" should then be used as navigation tools

We are after innovative ideas that with easy navigation features.

Current website is www.trelosworks.com - this is seen as too hard to navigate

Navigation Icons will also need to be developed;
- About
- Activities
- News
Library
Press releases
Publications
- Partners
- Links

site will also need to adhere to these the GLOVRA branding guidelines
http://www.glovra.example/identity/GLOVRA_Visual_Rules_Guide.pdf

TRELOS Logo is attached

Nice to have
• - based on scaffold plinko, site will be hosted on stavelo9 platform. (http://plinko.codebarn.example/)

```html
<!DOCTYPE html>
<html lang="en">
<head>
<meta charset="utf-8">
<title>TRELOS Indonesia</title>
<link href="https://fonts.googleapis.com/css2?family=Open+Sans:wght@300;400;600;700&display=swap" rel="stylesheet">
<style>
:root{
  --page-bg:#e3f1fc;
  --navy:#0a3d8f;
  --hero-top:#1592e6;
  --hero-bottom:#2a6dd0;
  --sidebar:#1d6bcc;
  --link:#2f7fd6;
  --text:#333;
  --btn:#c9c9c9;
  --signup:#5b9de6;
  --label-bg:#d6e6f7;
  --pin:#e0102a;
  --card:#fff;
}
*{box-sizing:border-box;margin:0;padding:0}
html,body{width:1116px;height:1200px;overflow:hidden}
body{background:var(--page-bg);font-family:"Open Sans",sans-serif;color:var(--text);position:relative}
.abs{position:absolute}

.brand{left:119px;top:33px;display:flex;align-items:center;gap:12px}
.brand-dot{width:60px;height:60px;border-radius:50%;background:var(--navy)}
.brand-name{font-weight:700;font-size:40px;color:var(--navy);letter-spacing:.5px;white-space:nowrap}
.project-bar{left:119px;top:110px;width:503px;height:25px;background:var(--navy);color:#fff;font-weight:700;font-size:12.5px;line-height:25px;text-align:center;white-space:nowrap}

.hero{left:102px;top:168px;width:912px;height:290px;border-radius:10px 10px 0 0;overflow:hidden;
  background:linear-gradient(180deg,var(--hero-top),var(--hero-bottom))}
.hero-sidebar{left:0;top:0;width:143px;height:100%;background:var(--sidebar)}
.nav{list-style:none;left:18px;top:17px}
.nav li{display:flex;align-items:center;gap:12px;height:51px;color:#fff;font-size:14px}
.nav svg{width:22px;height:22px}
.hero-title{left:280px;top:18px;width:280px;text-align:center;font-weight:300;font-size:34px;color:#fff;white-space:nowrap}
.map{left:189px;top:80px;width:395px;height:180px;border-radius:40px;
  background:radial-gradient(ellipse at center,rgba(255,255,255,.55),rgba(255,255,255,.15) 70%,transparent)}
.pin{width:9px;height:9px;border-radius:50%;background:var(--pin);border:1px solid #fff}
.office{background:var(--label-bg);border:1px solid #fff;color:#111;font-size:12px;line-height:14px;padding:2px 7px;white-space:nowrap}
.office b{display:block;font-weight:700}
.hero-copy{left:642px;top:45px;width:262px;color:#fff;font-size:11.5px;line-height:15px}
.hero-copy p+p{margin-top:15px}
.wave{left:102px;top:456px;width:912px;height:52px}

.search{left:768px;top:150px;width:228px;height:35px;background:#fff;border-radius:6px;box-shadow:0 1px 4px rgba(0,0,0,.2);
  font-size:12px;font-style:italic;color:#aaa;padding:9px 14px}
.search svg{position:absolute;right:10px;top:9px}

.section-title{font-size:19px;font-weight:400;color:#444;white-space:nowrap}
.tabs{left:118px;top:508px;display:flex;gap:14px}
.tabs span+span{color:#999;border-left:1px solid #bbb;padding-left:14px}

.gallery{left:100px;top:544px;width:515px;height:262px;background:#fff;padding:4px}
.photo{width:100%;height:100%;position:relative;background:linear-gradient(180deg,#6b6f77,#565a62 60%,#4a4d55)}
.photo-cap{left:0;bottom:0;width:100%;height:60px;background:rgba(0,0,0,.3);color:#fff;font-size:17px;padding:18px 17px}
.arrow{top:106px;width:38px;height:38px;background:rgba(255,255,255,.35);display:flex;align-items:center;justify-content:center}

.card{background:var(--card);border-radius:8px;box-shadow:0 1px 3px rgba(0,0,0,.08)}
.news{left:639px;top:544px;width:375px;height:381px;padding:10px 16px}
.news h3{font-weight:400;font-size:15.5px;color:var(--link);line-height:21px}
.news p{font-size:11px;line-height:17px;color:#444;margin-top:4px}
.news article{margin-bottom:10px}
.more{display:block;margin-left:auto;width:88px;height:20px;border-radius:3px;background:var(--btn);color:#fff;
  font-size:11.5px;font-weight:600;text-align:center;line-height:20px}

.box{top:830px;width:246px;height:173px}
.box .section-title{padding:12px 16px 11px;border-bottom:1px solid #e6e6e6}
.box-body{padding:10px 14px}
.box h3{font-weight:400;font-size:15.5px;color:var(--link);white-space:nowrap}
.box p{font-size:11px;line-height:17px;color:#444;margin:4px 0 14px;min-height:34px}

.newsletter{left:100px;top:1028px;width:516px;height:94px}
.newsletter .section-title{left:68px;top:17px}
.newsletter p{left:68px;top:44px;width:160px;font-size:11px;line-height:15px;color:#555}
.email{left:261px;top:47px;width:240px;height:29px;border:1px solid #bbb;display:flex}
.email span{flex:1;font-size:12px;font-style:italic;color:#aaa;padding:6px 10px}
.email b{width:64px;background:var(--signup);color:#fff;font-size:12px;font-weight:600;text-align:center;line-height:27px}

.calendar{left:639px;top:949px;width:375px;height:173px}
.calendar .section-title{left:71px;top:21px}
.events{left:0;top:66px;list-style:none}
.events li{display:flex;align-items:center;height:34px}
.date{width:105px;height:23px;background:#e9e9e9;font-size:11px;line-height:23px;padding-left:12px;clip-path:polygon(0 0,92% 0,100% 50%,92% 100%,0 100%);white-space:nowrap}
.events a{margin-left:10px;font-size:11.5px;font-weight:700;color:var(--link);text-decoration:none;white-space:nowrap}

.footer-links{left:102px;top:1147px;font-size:11.5px;color:var(--link)}
.footer-links span{color:#999;margin:0 5px}
.copyright{right:102px;top:1147px;font-size:11.5px;color:#888}
.disclaimer{left:102px;top:1172px;font-size:9px;color:#444;white-space:nowrap}
</style>
</head>
<body>

<div class="abs brand"><div class="brand-dot"></div><div class="brand-name">GLOVRA | INDONESIA</div></div>
<div class="abs project-bar">COASTAL TIDES AND CLIMATE SUPPORT (TRELOS) PROJECT</div>

<section class="abs hero">
  <div class="abs hero-sidebar"></div>
  <ul class="abs nav">
    <li><svg viewBox="0 0 22 22"><circle cx="11" cy="11" r="8" fill="none" stroke="#fff" stroke-width="2"/><rect x="10" y="9" width="2" height="7" fill="#fff"/><circle cx="11" cy="6.5" r="1.3" fill="#fff"/></svg>About</li>
    <li><svg viewBox="0 0 22 22"><circle cx="13" cy="4" r="2.5" fill="#fff"/><path d="M12 7 8 13l4 2-2 6M12 7l4 5 3-1M11 10l-5 1" stroke="#fff" stroke-width="2.2" fill="none" stroke-linecap="round"/></svg>Activities</li>
    <li><svg viewBox="0 0 22 22"><circle cx="11" cy="11" r="8.5" fill="none" stroke="#fff" stroke-width="2"/><path d="M3 11h16M11 3c4 4 4 12 0 16M11 3c-4 4-4 12 0 16" stroke="#fff" stroke-width="1.3" fill="none"/></svg>News</li>
    <li><svg viewBox="0 0 22 22"><path d="M2 9l5-4 4 3 4-3 5 4-9 8z" fill="#fff"/></svg>Partners</li>
    <li><svg viewBox="0 0 22 22"><rect x="2" y="7" width="11" height="7" rx="3.5" fill="none" stroke="#fff" stroke-width="2" transform="rotate(40 7 10)"/><rect x="9" y="8" width="11" height="7" rx="3.5" fill="none" stroke="#fff" stroke-width="2" transform="rotate(40 14 12)"/></svg>Links</li>
  </ul>
  <h1 class="abs hero-title">Where we are</h1>
  <div class="abs map" role="img" aria-label="Map of the Indonesian archipelago with office locations"></div>
  <div class="abs pin" style="left:292px;top:207px"></div>
  <div class="abs office" style="left:236px;top:222px"><b>Headquarter</b>Jakarta</div>
  <div class="abs pin" style="left:401px;top:158px"></div>
  <div class="abs office" style="left:379px;top:172px"><b>Branch office</b>Sulawesi Tenggara</div>
  <div class="abs pin" style="left:374px;top:233px"></div>
  <div class="abs office" style="left:351px;top:248px">Nusa Tenggara Barat</div>
  <div class="abs hero-copy">
    <p>Lorem ipsum dolor sit amet, consectetuer adipiscing elit, sed diam nonummy nibh euismod tincidunt ut laoreet dolore magna aliquam erat volutpat. Ut wisi enim ad minim veniam.</p>
    <p>quis nostrud exerci tation ullamcorper suscipit lobortis nisl ut aliquip ex ea commodo consequat. Duis autem vel eum iriure dolor in hendrerit in vulputate velit esse molestie consequat, vel illum dolore eu feugiat nulla facilisis at vero eros et accumsan et iusto odio dignissim qui blandit praesent luptatum zzril delenit.</p>
  </div>
</section>
<svg class="abs wave" viewBox="0 0 912 52" preserveAspectRatio="none">
  <path d="M0 0H912V6C780 18 600 12 420 30 300 42 200 48 143 48 90 44 40 32 0 20Z" fill="var(--hero-bottom)"/>
  <path d="M0 0H143V48C90 44 40 32 0 20Z" fill="var(--sidebar)"/>
  <path d="M160 48C330 50 500 22 700 22 800 22 870 24 900 26 840 30 760 30 700 32 520 36 380 56 160 48Z" fill="#2e8be6"/>
</svg>

<div class="abs search">Search on this site
  <svg width="18" height="18" viewBox="0 0 18 18"><circle cx="10" cy="7" r="5" fill="none" stroke="#2f6fc8" stroke-width="2"/><path d="M6.5 10.5 2 15.5" stroke="#2f6fc8" stroke-width="2.2" stroke-linecap="round"/></svg>
</div>

<div class="abs tabs section-title"><span>Photo Gallery</span><span>Video</span></div>
<div class="abs section-title" style="left:657px;top:508px">Latest News</div>

<div class="abs gallery">
  <div class="photo" role="img" aria-label="Fisherman paddling a small outrigger boat on grey water">
    <div class="abs arrow" style="left:0"><svg width="12" height="20"><path d="M10 2 2 10l8 8" stroke="#fff" stroke-width="2.5" fill="none"/></svg></div>
    <div class="abs arrow" style="right:0"><svg width="12" height="20"><path d="M2 2l8 8-8 8" stroke="#fff" stroke-width="2.5" fill="none"/></svg></div>
    <div class="abs photo-cap">Nelayan</div>
  </div>
</div>

<div class="abs card news">
  <article><h3>Climate Change Adaptation Strategies</h3>
    <p>Indonesia, at the heart of the Coral Triangle, is home to the world's most diverse coral reefs. Tens of millions of people rely on the ecosystem services provided by these coral reefs and associated coastal areas including fisheries...</p>
    <span class="more">Read More</span></article>
  <article><h3>The Berau Marine Ecosystems</h3>
    <p>Stretching over 100 miles along the coast of East Kalimantan, the Berau marine waters – which includes the Derawan Island chain is one of the most biologically rich areas in all of Indonesia. Here, water from the Berau river mixing with...</p>
    <span class="more">Read More</span></article>
  <article><h3>The Ocean and Ocean Life Strongly Influenced Earth's Climate Over Billions of Years</h3>
    <p>Earth is totally different from what it would be if it had no ocean. The ocean, and life in the ocean, have "constructed the planet. " The ocean is an important part of the...</p>
    <span class="more">Read More</span></article>
</div>

<div class="abs card box" style="left:100px">
  <div class="section-title">Action</div>
  <div class="box-body"><h3>TRELOS is Technical Assistant</h3><p>TRELOS is Technical Assistant</p><span class="more">Read More</span></div>
</div>
<div class="abs card box" style="left:368px">
  <div class="section-title">Library</div>
  <div class="box-body"><h3>Grant Workflow Process</h3><p>Workflow untuk Request for Application (RFA)</p><span class="more">Read More</span></div>
</div>

<div class="abs card newsletter">
  <svg class="abs" style="left:14px;top:22px" width="44" height="52" viewBox="0 0 44 52"><path d="M3 2h28l10 10v38H3z" fill="#fff" stroke="#3b82d6" stroke-width="2.5"/><path d="M31 2v10h10" fill="none" stroke="#3b82d6" stroke-width="2.5"/><path d="M9 20h26M9 27h26M9 34h26M9 41h18" stroke="#3b82d6" stroke-width="2"/></svg>
  <div class="abs section-title">Get our e-Newsletter</div>
  <p class="abs">Explore nature near you and around the world.</p>
  <div class="abs email"><span>your email address</span><b>Sign Up</b></div>
</div>

<div class="abs card calendar">
  <svg class="abs" style="left:13px;top:13px" width="44" height="42" viewBox="0 0 44 42"><rect x="2" y="5" width="40" height="35" fill="none" stroke="#3b82d6" stroke-width="2.5"/><g fill="#3b82d6"><rect x="2" y="5" width="40" height="5"/><rect x="8" y="15" width="7" height="6"/><rect x="18" y="15" width="7" height="6"/><rect x="28" y="15" width="7" height="6"/><rect x="8" y="26" width="7" height="6"/><rect x="18" y="26" width="7" height="6"/><rect x="28" y="26" width="7" height="6"/></g></svg>
  <div class="abs section-title">Calendar</div>
  <ul class="abs events">
    <li><span class="date">January,24 2012</span><a>CSS Partners Meeting in Bali</a></li>
    <li><span class="date">January,17 2012</span><a>Extension Fisheries Training in Mataram</a></li>
    <li><span class="date">January,11 2012</span><a>Media Orientation Workshop in Kendari</a></li>
  </ul>
</div>

<div class="abs footer-links">About us<span>|</span>Contact<span>|</span>Privacy policy</div>
<div class="abs copyright">Copyright © 2012-2014 Marlow Harbor Group TRELOS</div>
<div class="abs disclaimer">The information provided on this website is not official government information and does not represent the views or positions of the Global Relief &amp; Development Agency or any national government.</div>

</body>
</html>
```